birchwell hollow cattle company website

we would like a home page, an about us page, a page for sires, a page for dams, A sale page where we can list progreny for sale and a contact us. on the about us page we would like there to be a family picture. on the sires page we would like to have a picture of each sire, a description beside them and a link to their online profile at northern hereford registry. on the dam page we would like to have a picture of each dam, aswell as a description beside them aswell as a link to the northern hereford registry site. would like the website to very mobile phone friendly as expecting most traffic to be on phone. we would like the website to look and feel very mich like a farm, rustic, barbed wire and other farm feels. we would also like a frozen genetics pages where we can include pictures and descriptions of the sires and dams aswell as a price for embryos and semen. we need to website to be easy to maintain so we can update pictures and information as it changes, we would like there to be a feature so that people can sign up to be on our mailing list by giving us their mailing addess and email and full name
aswell as an area where they can send us a message to contact us.

leaving for work for 3 weeks in the canadian arctic will have limited ability to use the internet

Target Market(s)

other ranchers, farmers, cattlemen,

Industry/Entity Type

farming, agriculture, cattle

Coding

Coded - Design and coding required

Requirements
Must have
• about page, contact page, sires page, dams page, SALE page.
Nice to have
• country/farm vibe, barbed wire, wood,

```html
<!DOCTYPE html>
<html lang="en">
<head>
<meta charset="utf-8">
<title>Birchwell Hollow Cattle Company</title>
<link href="https://fonts.googleapis.com/css2?family=Oswald:wght@500;600;700&family=Inter:wght@400;500;600&display=swap" rel="stylesheet">
<style>
:root{
  --ink:#262422;
  --ink-soft:#3a3633;
  --paper:#ede9e2;
  --wood-a:#e6e0d6;
  --wood-b:#efebe4;
  --sand:#e2d4bf;
  --chip:#e4d9c8;
  --white:#ffffff;
  --text:#3b3835;
  --footer:#2b2a28;
  --muted:#cfcac3;
}
*{box-sizing:border-box;margin:0;padding:0}
html,body{width:1200px;height:4323px;overflow:hidden}
body{position:relative;background:var(--paper);font-family:"Inter",sans-serif;color:var(--text)}
.abs{position:absolute}
.display{font-family:"Oswald",sans-serif;font-weight:700;text-transform:uppercase;color:var(--ink);letter-spacing:.2px}
.btn{position:absolute;display:flex;align-items:center;justify-content:center;font-family:"Oswald",sans-serif;font-weight:600;text-transform:uppercase;background:var(--ink);color:var(--white);border-radius:6px}
.tag{display:inline-block;background:var(--ink);color:var(--white);padding:0 14px;border-radius:3px;transform:skewX(-4deg)}
.rule{position:absolute;height:3px;background:var(--ink)}
.photo{position:absolute}

/* header */
.site-header{left:0;top:0;width:1200px;height:155px;background:var(--paper)}
.brand{left:148px;top:40px;width:150px;text-align:center}
.brand-mark{width:34px;height:34px;background:var(--ink);margin:0 auto 8px;border-radius:3px}
.brand-name{font-family:"Oswald",sans-serif;font-weight:600;font-size:15px;line-height:1.15;color:var(--ink);text-transform:uppercase}
.follow{left:636px;top:43px;font-size:11px;font-family:"Oswald",sans-serif;color:var(--ink)}
.social-sq{top:36px;width:26px;height:26px;background:var(--ink);border-radius:5px}
.divider-v{left:838px;top:28px;width:1px;height:42px;background:#bdb6ad}
.call{left:905px;top:28px;font-family:"Oswald",sans-serif;color:var(--ink)}
.call small{display:block;font-size:14px;font-weight:500}
.call strong{display:block;font-size:21px;font-weight:600}
.nav{left:443px;top:90px;display:flex;gap:0;align-items:center}
.nav a{font-family:"Oswald",sans-serif;font-size:14px;font-weight:500;color:var(--ink);text-decoration:none;padding:7px 14px;text-transform:uppercase}
.nav a.active{background:var(--ink);color:var(--white);border-radius:6px}

/* hero */
.hero{left:0;top:155px;width:1200px;height:575px;background:linear-gradient(180deg,#5a6a74 0%,#7a5a45 35%,#6d3f26 60%,#a9874f 85%,#c7a868 100%)}
.hero-shade{left:0;top:155px;width:1200px;height:575px;background:rgba(20,14,10,.25)}
.hero-title{left:0;width:1200px;text-align:center;color:var(--white);font-family:"Oswald",sans-serif;font-weight:700;text-transform:uppercase}
.hero-sub{left:0;top:425px;width:1200px;text-align:center;color:var(--white);font-size:20px;line-height:29px}
.btn-light{background:var(--white);color:var(--ink);font-size:17px}
.dot{top:665px;width:10px;height:10px;border-radius:50%;background:var(--white)}

/* welcome */
.welcome-photo{left:148px;top:793px;width:479px;height:450px;border-radius:6px;background:linear-gradient(135deg,#6b4a33,#8a6a4f 55%,#3f3a34)}
.body-copy{font-size:13.5px;line-height:22.5px;color:var(--text)}

/* wood bands */
.wood{left:0;width:1200px;background:linear-gradient(180deg,var(--wood-b),var(--wood-a) 50%,var(--wood-b))}
.wire{left:0;width:1200px;height:14px}
.center-head{left:0;width:1200px;text-align:center}
.center-sub{left:0;width:1200px;text-align:center;font-size:15px;color:var(--text)}

/* genetics cards */
.gen-photo{top:1585px;width:437px;height:455px;border-radius:8px}
.gen-card{top:1948px;width:400px;height:202px;background:var(--white);border-radius:10px;box-shadow:0 4px 14px rgba(0,0,0,.08);padding:26px 34px}
.gen-card h3{font-family:"Oswald",sans-serif;font-size:24px;font-weight:700;color:var(--ink);margin-bottom:8px}
.gen-card p{font-size:11.5px;line-height:18px;color:var(--text)}

/* equipment */
.eq-card{top:2528px;width:214px;height:450px;background:var(--white);border-radius:10px;box-shadow:0 3px 12px rgba(0,0,0,.06)}
.eq-photo{position:absolute;left:7px;top:7px;width:200px;height:180px;border-radius:6px;background:linear-gradient(180deg,#cfd8de,#3f7b4e 55%,#5b5a4c)}
.eq-card h4{position:absolute;left:19px;top:205px;font-family:"Oswald",sans-serif;font-size:15px;font-weight:600;color:var(--ink);text-transform:uppercase}
.eq-card ul{position:absolute;left:19px;top:240px;width:180px;list-style:none}
.eq-card li{font-size:10.5px;line-height:15px;margin-bottom:11px;padding-left:13px;position:relative}
.eq-card li::before{content:"";position:absolute;left:0;top:4px;border-left:5px solid var(--ink);border-top:3.5px solid transparent;border-bottom:3.5px solid transparent}
.price{position:absolute;left:24px;top:357px;display:flex;align-items:center;gap:10px}
.price span{background:var(--chip);font-size:10.5px;padding:4px 8px;border-radius:3px}
.price strong{font-family:"Oswald",sans-serif;font-size:20px;font-weight:500;color:var(--ink)}
.eq-card .btn{left:24px;top:392px;width:88px;height:30px;font-size:11px;border-radius:4px}
.arrow{top:2736px;width:42px;height:42px;border:1.5px solid #8b857e;border-radius:50%}

/* frozen */
.frozen-photo{left:600px;top:3145px;width:365px;height:510px;background:linear-gradient(160deg,#5d4a3a,#2e3a5a 45%,#d9d6d1 75%,#8a7a63);clip-path:polygon(30% 4%,92% 0,86% 30%,96% 60%,78% 92%,40% 100%,8% 84%,0 50%,12% 20%)}

/* mailing */
.grass{left:0;top:3760px;width:1200px;height:160px;background:var(--ink)}
.mail-box{left:148px;top:3715px;width:900px;height:205px;background:var(--sand);border-radius:14px}
.field{position:absolute;height:46px;background:var(--white);border-radius:6px;font-size:13px;color:#555;display:flex;align-items:center;padding-left:18px}

/* footer */
.footer{left:0;top:3920px;width:1200px;height:403px;background:var(--footer);color:var(--white)}
.foot-head{font-family:"Inter",sans-serif;font-weight:600;font-size:13.5px;text-transform:uppercase;color:var(--white)}
.foot-line{width:32px;height:2px;background:var(--white);margin-top:9px}
.foot-list{font-size:12.5px;line-height:21.5px;color:var(--muted)}
.circle-icon{width:30px;height:30px;border:2px solid var(--white);border-radius:50%}
</style>
</head>
<body>

<!-- header -->
<header class="abs site-header">
  <div class="abs brand">
    <div class="brand-mark"></div>
    <div class="brand-name">Birchwell Hollow<br>Cattle Company</div>
  </div>
  <div class="abs follow">FOLLOW US</div>
  <div class="abs social-sq" style="left:706px"></div>
  <div class="abs social-sq" style="left:743px"></div>
  <div class="abs social-sq" style="left:780px"></div>
  <div class="abs divider-v"></div>
  <svg class="abs" style="left:858px;top:34px" width="36" height="36" viewBox="0 0 24 24" aria-hidden="true"><path fill="#262422" d="M6.6 10.8a15.1 15.1 0 0 0 6.6 6.6l2.2-2.2c.3-.3.7-.4 1-.2 1.1.4 2.3.6 3.6.6.6 0 1 .4 1 1V20c0 .6-.4 1-1 1A17 17 0 0 1 3 4c0-.6.4-1 1-1h3.5c.6 0 1 .4 1 1 0 1.3.2 2.5.6 3.6.1.3 0 .7-.2 1z"/></svg>
  <div class="abs call"><small>CALL US</small><strong>+1 888 888 8888</strong></div>
  <nav class="abs nav">
    <a class="active">Home</a><a>About Us</a><a>Sires</a><a>Dams</a><a>Cattle for Sale</a><a>Frozen Genetics</a><a>Contact Us</a>
  </nav>
</header>

<!-- hero -->
<section>
  <div class="photo hero abs" role="img" aria-label="Red angus bull standing in hay beside a steel corral fence"></div>
  <div class="abs hero-shade"></div>
  <div class="abs hero-title" style="top:285px;font-size:64px;line-height:70px">Raising Quality</div>
  <div class="abs hero-title" style="top:352px;font-size:48px;line-height:54px">Angus With Integrity</div>
  <div class="abs hero-sub">Birchwell Hollow Cattle Company – Premium<br>Genetics from Our Family to Yours</div>
  <div class="btn btn-light" style="left:432px;top:512px;width:165px;height:44px">View Our Sires</div>
  <div class="btn btn-light" style="left:632px;top:512px;width:167px;height:44px">Cattle for Sale</div>
  <div class="abs dot" style="left:558px;background:transparent;border:2px solid #fff"></div>
  <div class="abs dot" style="left:584px"></div>
  <div class="abs dot" style="left:609px"></div>
  <div class="abs dot" style="left:634px"></div>
</section>

<!-- welcome -->
<section>
  <div class="photo welcome-photo" role="img" aria-label="Family of four standing in front of a wooden barn"></div>
  <div class="abs display" style="left:662px;top:788px;font-size:26px;line-height:38px"><span class="tag">Welcome To</span></div>
  <h1 class="abs display" style="left:668px;top:836px;font-size:42px;line-height:47px;width:420px">Birchwell Hollow<br>Cattle Company</h1>
  <div class="rule" style="left:670px;top:956px;width:38px"></div>
  <p class="abs body-copy" style="left:670px;top:988px;width:385px">Lorem ipsum dolor sit amet, consectetur adipiscing elit, sed do eiusmod tempor incididunt ut labore et dolore magna aliqua. Ut enim ad minim veniam, quis nostrud exercitation ullamco laboris nisi ut aliquip ex ea commodo consequat. Duis aute irure dolor in reprehenderit in voluptate velit esse cillum dolore eu fugiat nulla pariatur. Excepteur sint occaecat cupidatat non proident, sunt in culpa qui officia deserunt mollit anim id est laboru</p>
  <div class="btn" style="left:672px;top:1201px;width:104px;height:40px;font-size:13px">Read More</div>
</section>

<!-- proven genetics -->
<section>
  <div class="abs wood" style="top:1330px;height:935px"></div>
  <svg class="abs wire" style="top:1330px" viewBox="0 0 1200 14" aria-hidden="true"><line x1="0" y1="5" x2="1200" y2="5" stroke="#6a6560" stroke-width="2"/><line x1="0" y1="9" x2="1200" y2="9" stroke="#6a6560" stroke-width="2"/></svg>
  <h2 class="abs display center-head" style="top:1420px;font-size:34px;line-height:48px">Proven Angus <span class="tag">Genetics</span></h2>
  <p class="abs center-sub" style="top:1484px">Our sires and dams are carefully selected for performance, temperament, and longevity.</p>
  <div class="rule" style="left:580px;top:1536px;width:40px"></div>

  <div class="photo gen-photo" style="left:148px;background:linear-gradient(180deg,#6e8a9c,#2c2a28 45%,#4d7a3a)" role="img" aria-label="Black angus cow grazing in a green pasture"></div>
  <div class="abs gen-card" style="left:166px"><h3>ANGUS</h3><p>Lorem ipscur adipiscing elit, sed do eiusmod tempor incid idunt ut labore et dolore magna aliqua dolores eos qui ratione .</p></div>
  <div class="btn" style="left:200px;top:2083px;width:102px;height:38px;font-size:12.5px">Read More</div>

  <div class="photo gen-photo" style="left:610px;background:linear-gradient(180deg,#3f5a3a,#7a3a26 45%,#e8e0d4 65%,#6a4a5a)" role="img" aria-label="Red and white hereford cow in a field"></div>
  <div class="abs gen-card" style="left:628px"><h3>SIRES</h3><p>Lorem ipsum dolor sit amet, consectetur adipiscing elit, sed do eiusmod tempor incid idunt ut labore et dolore magna aliqua dolores eos qui ratione .</p></div>
  <div class="btn" style="left:662px;top:2083px;width:102px;height:38px;font-size:12.5px">Read More</div>
  <svg class="abs wire" style="top:2256px" viewBox="0 0 1200 14" aria-hidden="true"><line x1="0" y1="5" x2="1200" y2="5" stroke="#6a6560" stroke-width="2"/><line x1="0" y1="9" x2="1200" y2="9" stroke="#6a6560" stroke-width="2"/></svg>
</section>

<!-- equipment -->
<section>
  <h2 class="abs display center-head" style="top:2354px;font-size:34px;line-height:48px">Equipment <span class="tag">Sales</span></h2>
  <p class="abs center-sub" style="top:2420px;font-size:14.5px">We are excited so be supplying quality livestock equipment products to interior of BC and surrounding areas.</p>
  <div class="rule" style="left:577px;top:2470px;width:40px"></div>

  <svg class="abs arrow" style="left:65px" viewBox="0 0 42 42" aria-hidden="true"><path d="M24 14l-7 7 7 7" fill="none" stroke="#8b857e" stroke-width="1.8"/></svg>
  <svg class="abs arrow" style="left:1086px" viewBox="0 0 42 42" aria-hidden="true"><path d="M18 14l7 7-7 7" fill="none" stroke="#8b857e" stroke-width="1.8"/></svg>

  <div class="abs eq-card" style="left:148px">
    <div class="eq-photo" role="img" aria-label="Green single bale feeder"></div>
    <h4>Single Bale Feeder</h4>
    <ul><li>82" wide by 7' long</li><li>Robust design for longevity</li><li>Reduced wasted feed over traditional designs</li></ul>
    <div class="price"><span>Priced at</span><strong>$950</strong></div>
    <div class="btn">View Details</div>
  </div>
  <div class="abs eq-card" style="left:377px">
    <div class="eq-photo" style="background:linear-gradient(180deg,#e6e9ec,#2f4a3a 50%,#cfd3d6)" role="img" aria-label="Double bale feeder in snow"></div>
    <h4>Double Bale Feeder</h4>
    <ul><li>82" wide by 7' long</li><li>Robust design for longevity</li><li>Reduced wasted feed over traditional designs</li></ul>
    <div class="price"><span>Priced at</span><strong>$1400</strong></div>
    <div class="btn">View Details</div>
  </div>
  <div class="abs eq-card" style="left:606px">
    <div class="eq-photo" style="background:linear-gradient(180deg,#7f9fc2,#dfe4ea 40%,#3d7d55 70%,#e5e8ea)" role="img" aria-label="Triple bale feeder on a snowy yard"></div>
    <h4>Triple Bale Feeder</h4>
    <ul><li>82" wide by 7' long</li><li>Robust design for longevity</li><li>Reduced wasted feed over traditional designs</li></ul>
    <div class="price"><span>Priced at</span><strong>$1800</strong></div>
    <div class="btn">View Details</div>
  </div>
  <div class="abs eq-card" style="left:835px">
    <div class="eq-photo" style="background:linear-gradient(180deg,#a8b4bd,#4a3e34 45%,#6b5a48)" role="img" aria-label="Row of silage bunks with cattle feeding"></div>
    <h4>24' Silage Bunks</h4>
    <ul><li>82" wide by 7' long</li><li>Robust design for longevity</li><li>Reduced wasted feed over traditional designs</li></ul>
    <div class="price"><span>Priced at</span><strong>$1050</strong></div>
    <div class="btn">View Details</div>
  </div>
</section>

<!-- frozen genetics -->
<section>
  <div class="abs wood" style="top:3062px;height:700px"></div>
  <svg class="abs wire" style="top:3062px" viewBox="0 0 1200 14" aria-hidden="true"><line x1="0" y1="5" x2="1200" y2="5" stroke="#6a6560" stroke-width="2"/><line x1="0" y1="9" x2="1200" y2="9" stroke="#6a6560" stroke-width="2"/></svg>
  <h2 class="abs display" style="left:132px;top:3218px;font-size:34px;line-height:48px"><span class="tag">Frozen Genetics</span> Program</h2>
  <div class="rule" style="left:152px;top:3300px;width:38px"></div>
  <p class="abs body-copy" style="left:152px;top:3340px;width:385px">Lorem ipsum dolor sit amet, consectetur adipiscing elit, sed do eiusmod tempor incididunt ut labore et dolore magna aliqua. Ut enim ad minim veniam, quis nostrud exercitation ullamco laboris nisi ut aliquip ex ea commodo consequat. Duis aute irure dolor in reprehenderit in voluptate velit esse cillum dolore eu fugiat nulla pariatur. Excepteur sint occaecat cupidatat non proident, sunt in culpa qui officia deserunt mollit anim id est laboru</p>
  <div class="btn" style="left:152px;top:3590px;width:104px;height:40px;font-size:13px">Read More</div>
  <div class="photo frozen-photo" role="img" aria-label="Rancher with a semen storage tank beside cattle in a barn"></div>
</section>

<!-- mailing list -->
<section>
  <div class="abs grass"></div>
  <div class="abs mail-box">
    <h2 class="abs display" style="left:35px;top:38px;font-size:32px;line-height:46px">Join Our <span class="tag">Mailing List</span></h2>
    <p class="abs" style="left:35px;top:118px;width:290px;font-size:15px;line-height:24px;color:var(--text)">Stay informed about upcoming sales, genetics releases, and farm updates.</p>
    <div class="field" style="left:396px;top:44px;width:230px">Full Name</div>
    <div class="field" style="left:640px;top:44px;width:230px">Email</div>
    <div class="field" style="left:396px;top:110px;width:230px">Location</div>
    <div class="btn" style="left:640px;top:110px;width:230px;height:46px;font-size:17px">Subscribe</div>
  </div>
</section>

<!-- footer -->
<footer class="abs footer">
  <div class="abs" style="left:140px;top:90px;width:250px;text-align:center">
    <div style="width:54px;height:54px;background:var(--white);margin:0 auto 14px;border-radius:4px"></div>
    <div style="font-family:'Oswald',sans-serif;font-weight:600;font-size:28px;line-height:34px;text-transform:uppercase;color:var(--white)">Birchwell Hollow<br>Cattle Company</div>
  </div>

  <div class="abs" style="left:468px;top:73px">
    <div class="foot-head">Contact Us</div><div class="foot-line"></div>
  </div>
  <svg class="abs" style="left:470px;top:127px" width="11" height="14" viewBox="0 0 12 16" aria-hidden="true"><path fill="#fff" d="M6 0a6 6 0 0 0-6 6c0 4.5 6 10 6 10s6-5.5 6-10a6 6 0 0 0-6-6zm0 8.2A2.2 2.2 0 1 1 6 3.8a2.2 2.2 0 0 1 0 4.4z"/></svg>
  <div class="abs foot-list" style="left:498px;top:118px;line-height:17px;color:var(--white)">72 Fenwick Line, Harlow Bend,<br>ON, K0L 2P5</div>
  <svg class="abs" style="left:470px;top:178px" width="12" height="12" viewBox="0 0 24 24" aria-hidden="true"><path fill="#fff" d="M6.6 10.8a15.1 15.1 0 0 0 6.6 6.6l2.2-2.2c.3-.3.7-.4 1-.2 1.1.4 2.3.6 3.6.6.6 0 1 .4 1 1V20c0 .6-.4 1-1 1A17 17 0 0 1 3 4c0-.6.4-1 1-1h3.5c.6 0 1 .4 1 1 0 1.3.2 2.5.6 3.6.1.3 0 .7-.2 1z"/></svg>
  <div class="abs foot-list" style="left:498px;top:173px;color:var(--white)">+1 888 888 8888</div>
  <svg class="abs" style="left:470px;top:213px" width="13" height="10" viewBox="0 0 14 10" aria-hidden="true"><rect width="14" height="10" rx="1" fill="#fff"/><path d="M0 1l7 5 7-5" fill="none" stroke="#2b2a28" stroke-width="1.3"/></svg>
  <div class="abs foot-list" style="left:498px;top:207px;color:var(--white)">info@birchwellhollow.com</div>

  <div class="abs" style="left:712px;top:73px">
    <div class="foot-head">Menu</div><div class="foot-line"></div>
    <div class="foot-list" style="margin-top:14px;color:var(--white)">About Us<br>Sires<br>Dams<br>Cattle for Sale<br>Frozen Genetics<br>Contact Us</div>
  </div>

  <div class="abs" style="left:875px;top:73px">
    <div class="foot-head">Follow Us</div><div class="foot-line"></div>
    <div style="display:flex;gap:6px;margin-top:18px">
      <div class="circle-icon"></div><div class="circle-icon"></div><div class="circle-icon"></div><div class="circle-icon"></div><div class="circle-icon"></div>
    </div>
  </div>

  <div class="abs" style="left:148px;top:308px;width:900px;height:1px;background:#5a5754"></div>
  <div class="abs" style="left:0;top:357px;width:1200px;text-align:center;font-size:11px;color:var(--muted)">Copyright © 2026 All Rights Reserved</div>
</footer>

</body>
</html>
```